Graphic- Educational Visual

Brisko Dog Training has created an educational tool to help its students understand and prioritize some key concepts in their dog training.

We are requesting a visual of this tool be designed.

Name/title of tool (to be included in graphic): The Brisko Pathway
Description: Funnel (inverted pyramid).

From top to bottom, the levels are called:

Connect
Develop
Progress
Refine

The diagram should also include a cycle around it to, to represent that one is always moving through the levels.

Business colours are included below to make sure the funnel's colours complement the website colours or at least don't clash:

#0AA1C7 Blue and #7FC31B Green
Purple as a secondary colour -75279C

For reference, business logo is attached.

Dog Training

```html
<!DOCTYPE html>
<html lang="en">
<head>
<meta charset="utf-8">
<title>The Brisko Pathway – Brisko Dog Training</title>
<link rel="stylesheet" href="https://fonts.googleapis.com/css2?family=Montserrat:wght@700;800&display=swap">
<style>
  :root {
    --brand-blue: #19a1c7;
    --brand-green: #7fc241;
    --ink-dark: #3f3f3f;
    --paper: #ffffff;
    --label: #ffffff;
  }
  html, body {
    margin: 0;
    padding: 0;
    width: 1200px;
    height: 1200px;
    overflow: hidden;
    background: var(--paper);
  }
  .pathway-canvas {
    display: block;
    width: 1200px;
    height: 1200px;
  }
  .tool-title {
    font-family: "Montserrat", sans-serif;
    font-weight: 800;
    font-size: 66px;
    fill: var(--brand-blue);
  }
  .level-label {
    font-family: "Montserrat", sans-serif;
    font-weight: 700;
    font-size: 30px;
    letter-spacing: 1px;
    fill: var(--label);
  }
  .band-blue { fill: var(--brand-blue); }
  .band-green { fill: var(--brand-green); }
  .band-fold { fill: var(--ink-dark); }
  .cycle-arc { fill: none; stroke-width: 48; }
  .icon-line { fill: none; stroke: var(--label); stroke-width: 4; stroke-linecap: round; stroke-linejoin: round; }
  .icon-fill { fill: var(--label); }
</style>
</head>
<body>
<svg class="pathway-canvas" viewBox="0 0 1500 1500" xmlns="http://www.w3.org/2000/svg" aria-labelledby="pathway-title">
  <title id="pathway-title">The Brisko Pathway: Connect, Develop, Progress, Refine, in a continuous cycle</title>
  <defs>
    <linearGradient id="fade-green" gradientUnits="userSpaceOnUse" x1="0" y1="990" x2="0" y2="760">
      <stop offset="0" stop-color="#7fc241" stop-opacity="0"/>
      <stop offset="1" stop-color="#7fc241"/>
    </linearGradient>
    <linearGradient id="fade-blue" gradientUnits="userSpaceOnUse" x1="800" y1="440" x2="1010" y2="560">
      <stop offset="0" stop-color="#19a1c7" stop-opacity="0"/>
      <stop offset="1" stop-color="#19a1c7"/>
    </linearGradient>
    <linearGradient id="fade-dark" gradientUnits="userSpaceOnUse" x1="1070" y1="1090" x2="880" y2="1230">
      <stop offset="0" stop-color="#3f3f3f" stop-opacity="0"/>
      <stop offset="1" stop-color="#3f3f3f"/>
    </linearGradient>
  </defs>

  <!-- Title -->
  <text class="tool-title" x="750" y="310" text-anchor="middle">The Brisko Pathway</text>

  <!-- Cycle -->
  <g class="cycle">
    <path class="cycle-arc" stroke="url(#fade-green)" d="M 370,998 A 408 408 0 0 1 752,437"/>
    <polygon fill="var(--brand-green)" points="750,385 805,438 750,492"/>

    <path class="cycle-arc" stroke="url(#fade-blue)" d="M 805,441 A 408 408 0 0 1 1098,1050"/>
    <polygon fill="var(--brand-blue)" points="1053,1022 1145,1077 1070,1095"/>

    <path class="cycle-arc" stroke="url(#fade-dark)" d="M 1060,1107 A 408 408 0 0 1 402,1058"/>
    <polygon fill="var(--ink-dark)" points="443,1020 370,998 350,1072"/>
  </g>

  <!-- Funnel folds -->
  <g class="funnel-folds">
    <polygon class="band-fold" points="778,731 1018,731 778,800 510,800"/>
    <polygon class="band-fold" points="778,870 958,870 778,939 570,939"/>
    <polygon class="band-fold" points="778,1009 898,1009 778,1079 632,1079"/>
  </g>

  <!-- Funnel levels -->
  <g class="funnel-level level-connect">
    <polygon class="band-blue" points="448,661 1049,661 1020,731 478,731"/>
    <g class="icon-link" transform="translate(658,695) rotate(-45)">
      <rect class="icon-line" x="-16" y="-6" width="18" height="12" rx="6"/>
      <rect class="icon-line" x="-2" y="-6" width="18" height="12" rx="6"/>
    </g>
    <text class="level-label" x="689" y="706">CONNECT</text>
  </g>

  <g class="funnel-level level-develop">
    <polygon class="band-green" points="510,800 988,800 958,870 540,870"/>
    <path class="icon-fill" d="M662,851 L646,835 C638,826 645,818 653,819 C657,819 660,822 662,825 C664,822 667,819 671,819 C679,818 686,826 678,835 Z"/>
    <text class="level-label" x="694" y="845">DEVELOP</text>
  </g>

  <g class="funnel-level level-progress">
    <polygon class="band-blue" points="570,939 928,939 898,1009 600,1009"/>
    <polyline class="icon-line" points="642,986 652,974 656,980 665,965"/>
    <polygon class="icon-fill" points="658,963 668,960 667,971"/>
    <text class="level-label" x="678" y="984">PROGRESS</text>
  </g>

  <g class="funnel-level level-refine">
    <polygon class="band-green" points="632,1079 866,1079 836,1148 662,1148"/>
    <circle class="icon-line" cx="678" cy="1121" r="7" stroke-dasharray="3 2"/>
    <circle class="icon-line" cx="678" cy="1121" r="2.5"/>
    <circle class="icon-line" cx="691" cy="1104" r="5" stroke-dasharray="3 2"/>
    <text class="level-label" x="710" y="1125">REFINE</text>
  </g>
</svg>
</body>
</html>
```